Business Card Re-Design/Update

We'd like to update out business cards. I've included our current "Style guide" which has the colour scheme of the organisation in it. I've also included the branding files with logos etc in them.

I've also included a copy of one of our existing cards so that you can see how ugly/dated they look. I'd like a fresh modern corporate look.

Target Market(s)

These are for our clients, potential clients, industry contacts - like all business cards

Contact Information for Business Card

Name
Position
Company Address - Level 1, 47 Fernby Street, Carlow Qld 4072
Direct Phone
mobile
Email
Website -www.korvalit.com.au
Logo

Colors

Designer to choose colors to be used in the design.

Requirements
Must have
• Main Logo
• Cards will need to be editable to be able to personalize them for each new employee.
Nice to have
• The MapOut, ShipWell, KeepSteady would be okay to have if they can be sensibly and professionally added to the look without detracting from the main imagery.
• Maybe they could go on the back of the card? will leave this to your creative discretion as to whether/where they fit.
Should not have
• Should not have decorative or script fonts

```html
<!DOCTYPE html>
<html lang="en">
<head>
<meta charset="utf-8">
<title>korvalIT business card</title>
<link rel="stylesheet" href="https://fonts.googleapis.com/css2?family=Roboto:wght@400;500;700&family=Roboto+Condensed:wght@400;700&display=swap">
<style>
:root{
  --backdrop:#2b2b2b;
  --paper:#f4f4f4;
  --brand-red:#c8161d;
  --brand-red-light:#db2027;
  --ink:#2a2a2a;
  --ink-soft:#555555;
  --rule:#c9c9c9;
  --white:#ffffff;
}
*{margin:0;padding:0;box-sizing:border-box}
html,body{width:1200px;height:960px;overflow:hidden;background:var(--backdrop)}
.canvas{position:relative;width:1200px;height:960px}
.card{position:absolute;left:320px;width:600px;height:342px}
.card-front{top:100px;background:var(--paper)}
.card-back{top:493px;background:radial-gradient(ellipse at 50% 45%,var(--brand-red-light) 0%,var(--brand-red) 75%)}

.brand{position:absolute;left:52px;top:168px;display:flex;align-items:center;gap:12px}
.brand-mark{width:34px;height:34px;background:var(--brand-red)}
.brand-name{font-family:"Roboto",sans-serif;font-weight:500;font-size:29px;color:var(--ink);letter-spacing:-0.3px}

.divider{position:absolute;left:311px;top:80px;width:1px;height:205px;background:var(--rule)}

.details{position:absolute;left:340px;top:72px;font-family:"Roboto",sans-serif;color:var(--ink-soft)}
.person-name{font-family:"Roboto Condensed",sans-serif;font-weight:700;font-size:21px;color:var(--brand-red);line-height:26px}
.person-role{font-family:"Roboto Condensed",sans-serif;font-size:15px;color:var(--ink);line-height:18px}
.address{font-size:14px;line-height:18px;margin-top:10px}
.contacts{list-style:none;margin-top:9px;font-size:14px;line-height:19px}
.contacts li{display:flex;align-items:center;gap:9px}
.contacts svg{width:13px;height:13px;fill:var(--brand-red);flex:none}

.back-mark{position:absolute;left:240px;top:70px;width:120px;height:120px;background:var(--white)}
.services{position:absolute;left:0;right:0;top:272px;display:flex;justify-content:center;gap:36px;list-style:none}
.services li{display:flex;align-items:center;gap:8px;font-family:"Roboto",sans-serif;font-weight:500;font-size:26px;color:var(--white)}
.service-dot{width:20px;height:20px;background:var(--white)}
</style>
</head>
<body>
<main class="canvas">
  <section class="card card-front" aria-label="Card front">
    <div class="brand">
      <span class="brand-mark"></span>
      <span class="brand-name">korvalIT</span>
    </div>
    <span class="divider"></span>
    <div class="details">
      <p class="person-name">MAREN HOLT</p>
      <p class="person-role">Business Development Manager</p>
      <p class="address">Level 1, 47 Fernby Street,<br>Carlow Qld 4072</p>
      <ul class="contacts">
        <li><svg viewBox="0 0 24 24"><path d="M6.6 10.8a15 15 0 0 0 6.6 6.6l2.2-2.2c.3-.3.7-.4 1-.2 1.1.4 2.3.6 3.6.6.6 0 1 .4 1 1V20c0 .6-.4 1-1 1A17 17 0 0 1 3 4c0-.6.4-1 1-1h3.5c.6 0 1 .4 1 1 0 1.3.2 2.5.6 3.6.1.3 0 .7-.2 1z"/></svg>+61 (0)7 5550 1200</li>
        <li><svg viewBox="0 0 24 24"><path d="M6.6 10.8a15 15 0 0 0 6.6 6.6l2.2-2.2c.3-.3.7-.4 1-.2 1.1.4 2.3.6 3.6.6.6 0 1 .4 1 1V20c0 .6-.4 1-1 1A17 17 0 0 1 3 4c0-.6.4-1 1-1h3.5c.6 0 1 .4 1 1 0 1.3.2 2.5.6 3.6.1.3 0 .7-.2 1z"/></svg>+61 (0)7 5550 1216</li>
        <li><svg viewBox="0 0 24 24"><path d="M7 1h10a2 2 0 0 1 2 2v18a2 2 0 0 1-2 2H7a2 2 0 0 1-2-2V3a2 2 0 0 1 2-2zm0 3v14h10V4z"/></svg>+61 (0)400 555 318</li>
        <li><svg viewBox="0 0 24 24"><path d="M6 2h12v6H6zM3 9h18a2 2 0 0 1 2 2v7h-4v4H5v-4H1v-7a2 2 0 0 1 2-2zm4 8v3h10v-3z"/></svg>+61 (0)7 5550 1203</li>
        <li><svg viewBox="0 0 24 24"><path d="M2 5h20v2l-10 6L2 7zm0 4l10 6 10-6v10H2z"/></svg>mholt@korvalit.com.au</li>
        <li><svg viewBox="0 0 24 24"><path d="M12 2a10 10 0 1 0 0 20 10 10 0 0 0 0-20zm-1 17.9A8 8 0 0 1 4.2 10L9 14.8v1a2 2 0 0 0 2 2zm6.9-2.5A2 2 0 0 0 16 16h-1v-3a1 1 0 0 0-1-1H8v-2h2a1 1 0 0 0 1-1V7h2a2 2 0 0 0 2-2v-.4a8 8 0 0 1 2.9 12.8z"/></svg>www.korvalit.com.au</li>
      </ul>
    </div>
  </section>

  <section class="card card-back" aria-label="Card back">
    <span class="back-mark"></span>
    <ul class="services">
      <li><span class="service-dot"></span>MapOut</li>
      <li><span class="service-dot"></span>ShipWell</li>
      <li><span class="service-dot"></span>KeepSteady</li>
    </ul>
  </section>
</main>
</body>
</html>
```